Business Card Design: recruitment/consultancy for business Thrive360onward

We need a business card design for a new company based in Adelaide Australia called Thrive360onward. Our Business aims to support people over 50 who may be looking for a career change, have been made redundant or generally looking for employment. We will also be working with businesses to provide them with recruiting solutions, job design, recruitment strategies and customised training. we will also be working with volunteering opportunities for those over 50.
We would like to see the E in thrive360onward strong and dominant. The final design should reflect change for the better, better opportunities, today is the day, make way for the new, all aimed at the 50 plus age group.
Colours we are thinking off include green (money, growth) black and white.... we like the idea of black and white photography with a one dominant colour...think of a of a black and white photo of a woman with dominant red lips...that sort of look

Business

Contact Information for Business Card

Kim, Mavis & Gwen
phone: 0439615028
Thrive360onward@mailbox-example.net
Social/Thrive360onward
www.thrive360onward-example.com.au

```html
<!DOCTYPE html>
<html lang="en">
<head>
<meta charset="utf-8">
<title>Thrive360onward – Business Card</title>
<link rel="stylesheet" href="https://fonts.googleapis.com/css2?family=Arimo:wght@400;700&display=swap">
<style>
  :root {
    --stage: #e9e6e2;
    --card: #ffffff;
    --card-shade: #f1f1f1;
    --ink: #1d1d1d;
    --muted: #555555;
    --accent: #d3242b;
    --band: #3b3435;
    --rule: #2a2a2a;
  }
  * { box-sizing: border-box; margin: 0; padding: 0; }
  html, body { width: 1200px; height: 858px; overflow: hidden; }
  body {
    background: var(--stage);
    font-family: "Arimo", Arial, sans-serif;
    position: relative;
  }
  .card {
    position: absolute;
    top: 275px;
    width: 540px;
    height: 309px;
    background: linear-gradient(135deg, var(--card) 0%, var(--card) 60%, var(--card-shade) 100%);
    box-shadow: 0 6px 18px rgba(0,0,0,0.18);
    overflow: hidden;
  }
  .card--front { left: 40px; }
  .card--back { left: 620px; }

  .brand-name {
    position: absolute;
    font-weight: 700;
    font-size: 20px;
    letter-spacing: -0.3px;
    color: var(--ink);
    white-space: nowrap;
  }
  .partners {
    position: absolute;
    color: var(--accent);
    font-size: 24px;
    font-weight: 400;
    line-height: 1.05;
  }
  .rule {
    position: absolute;
    height: 1px;
    background: var(--rule);
  }

  /* front */
  .portrait {
    position: absolute;
    top: 0;
    right: 0;
    width: 215px;
    height: 185px;
    background: linear-gradient(160deg, #dcdcdc 0%, #a9a9a9 55%, #3a3a3a 100%);
    clip-path: polygon(22% 0, 100% 0, 100% 100%, 0 100%, 0 58%);
  }
  .card--front .brand-name { top: 26px; left: 160px; }
  .card--front .partners { top: 88px; left: 30px; }
  .card--front .rule { top: 150px; left: 30px; width: 295px; }
  .contact-list {
    position: absolute;
    top: 196px;
    left: 205px;
    list-style: none;
    font-size: 13px;
    color: var(--muted);
    line-height: 19px;
  }
  .contact-list li { display: flex; align-items: center; gap: 8px; white-space: nowrap; }
  .contact-list svg { width: 11px; height: 11px; flex: none; }

  /* back */
  .card--back .partners { top: 30px; left: 30px; }
  .card--back .rule { top: 212px; left: 30px; width: 480px; height: 1px; background: #999; }
  .card--back .brand-name { top: 183px; right: 30px; }
  .web-band {
    position: absolute;
    left: 0;
    bottom: 0;
    width: 100%;
    height: 66px;
    background: var(--band);
    display: flex;
    align-items: center;
    padding-left: 30px;
  }
  .web-band span { color: var(--accent); font-size: 15px; }
</style>
</head>
<body>

<section class="card card--front">
  <div class="portrait" role="img" aria-label="Black and white portrait photograph with a single accent of red lips"></div>
  <div class="brand-name">Thrive360onward</div>
  <div class="partners">Kim,<br>Mavis &amp; Gwen</div>
  <div class="rule"></div>
  <ul class="contact-list">
    <li>
      <svg viewBox="0 0 12 12" aria-hidden="true"><path d="M3 1 L5 3 L4 4.5 Q5 7 7.5 8 L9 7 L11 9 L9.5 11 Q3 10 1 2.5 Z" fill="#555"/></svg>
      0439615028
    </li>
    <li>
      <svg viewBox="0 0 12 12" aria-hidden="true"><rect x="1" y="2.5" width="10" height="7" fill="none" stroke="#555" stroke-width="1.2"/><path d="M1 2.5 L6 7 L11 2.5" fill="none" stroke="#555" stroke-width="1.2"/></svg>
      Thrive360onward@mailbox-example.net
    </li>
    <li>
      <svg viewBox="0 0 12 12" aria-hidden="true"><circle cx="6" cy="6" r="5" fill="#555"/></svg>
      Social/Thrive360onward
    </li>
    <li>
      <svg viewBox="0 0 12 12" aria-hidden="true"><circle cx="6" cy="6" r="5" fill="none" stroke="#555" stroke-width="1.1"/><ellipse cx="6" cy="6" rx="2.2" ry="5" fill="none" stroke="#555" stroke-width="0.9"/><path d="M1 6 H11" stroke="#555" stroke-width="0.9"/></svg>
      www.thrive360onward-example.com.au
    </li>
  </ul>
</section>

<section class="card card--back">
  <div class="partners">Kim,<br>Mavis &amp; Gwen</div>
  <div class="brand-name">Thrive360onward</div>
  <div class="rule"></div>
  <div class="web-band"><span>www.thrive360onward-example.com.au</span></div>
</section>

</body>
</html>
```